professional business card design

Business card design. Photos have been uploaded and i am open to the designer choosing which photos to use. Would like the card to be mostyly in a grey scale design with black, whites, silver & grey colours. I have added copy of our flyer as would like on the back side of card our services to be listed. Do not use any bright colurs such as blue red green or yellow. i need to be able to edit the phone number and naem in the final card design submitted.

Target Market(s)

Clients

Industry/Entity Type

earhmovibng and transport

Contact Information for Business Card

Director Name, address, email, phone number and services

Colors

Designer to choose only greyscale colors for use in the design.

Requirements
Should not have
• no yellow, red, blue or green

```html
<!DOCTYPE html>
<html lang="en">
<head>
<meta charset="utf-8">
<title>Ridgeline Haulage Services – Business Card</title>
<link rel="stylesheet" href="https://fonts.googleapis.com/css2?family=Exo+2:wght@600;700;800&family=Roboto:wght@400;500&display=swap">
<style>
  :root {
    --page: #d6d6d6;
    --card: #0c0c0c;
    --card-hi: #262626;
    --silver-a: #f4f4f4;
    --silver-b: #b9b9b9;
    --silver-c: #8e8e8e;
    --white: #ffffff;
    --ink: #111111;
    --logo: #c9c9c9;
    --photo-light: #9a9a9a;
    --photo-dark: #5c5c5c;
  }
  * { margin: 0; padding: 0; box-sizing: border-box; }
  html, body { width: 900px; height: 1200px; overflow: hidden; }
  body { background: var(--page); position: relative; font-family: "Roboto", Arial, sans-serif; }

  .card {
    position: absolute; left: 78px; width: 744px; height: 440px;
    border-radius: 26px; overflow: hidden;
    background: radial-gradient(ellipse at 40% 35%, var(--card-hi) 0%, var(--card) 70%);
    box-shadow: 0 6px 14px rgba(0,0,0,.35);
  }
  .card--front { top: 132px; }
  .card--back { top: 638px; }

  /* front */
  .brand {
    position: absolute; left: 58px; top: 178px; width: 300px;
    font-family: "Exo 2", sans-serif; font-weight: 800; font-size: 96px;
    line-height: 1; color: var(--logo); letter-spacing: 6px;
  }
  .divider { position: absolute; left: 390px; top: 163px; width: 2px; height: 128px; background: var(--silver-b); }
  .person { position: absolute; left: 420px; top: 154px; color: var(--white); font-family: "Exo 2", sans-serif; }
  .person__name { font-size: 25px; font-weight: 700; letter-spacing: .5px; line-height: 1.1; }
  .person__role { font-size: 15px; font-weight: 600; }
  .contacts { position: absolute; left: 424px; top: 222px; list-style: none; color: var(--white); font-family: "Exo 2", sans-serif; font-weight: 600; font-size: 16px; }
  .contacts li { display: flex; align-items: center; height: 23px; }
  .contacts svg { width: 14px; height: 14px; margin-right: 17px; fill: var(--white); }
  .depot-band {
    position: absolute; left: 0; top: 333px; width: 100%; height: 38px;
    background: linear-gradient(90deg, var(--silver-b), var(--silver-a) 30%, var(--silver-a) 70%, var(--silver-b));
    color: var(--ink); font-family: "Exo 2", sans-serif; font-weight: 700; font-size: 16.5px;
    line-height: 38px; padding-left: 60px; letter-spacing: .4px;
  }

  /* back */
  .photo {
    position: absolute; inset: 0;
    clip-path: polygon(0 0, 480px 0, 300px 100%, 0 100%);
    background: linear-gradient(160deg, var(--photo-light) 0%, var(--photo-dark) 100%);
  }
  .services-banner {
    position: absolute; left: 420px; top: 42px; width: 324px; height: 44px;
    clip-path: polygon(28px 0, 100% 0, 100% 100%, 0 100%);
    background: linear-gradient(90deg, var(--silver-c), var(--silver-a) 35%, var(--white));
  }
  .services-title {
    position: absolute; right: 32px; top: 42px; height: 44px; line-height: 44px;
    font-family: "Exo 2", sans-serif; font-weight: 700; font-size: 25px; color: var(--ink);
  }
  .services { position: absolute; right: 24px; top: 102px; list-style: none; text-align: right; color: var(--white); font-size: 15px; }
  .services li { height: 28.9px; display: flex; justify-content: flex-end; align-items: center; }
  .services li::after { content: ""; width: 9px; height: 9px; background: var(--white); margin-left: 13px; }
</style>
</head>
<body>
  <section class="card card--front">
    <div class="brand">RHS</div>
    <div class="divider"></div>
    <div class="person">
      <div class="person__name">DANIEL HARROW</div>
      <div class="person__role">Director</div>
    </div>
    <ul class="contacts">
      <li><svg viewBox="0 0 16 16"><path d="M2 6c0-2 2-3 6-3s6 1 6 3v1h-3V6H5v1H2zM3 8h10l1 5H2z"/></svg>000 555 000</li>
      <li><svg viewBox="0 0 16 16"><path d="M1 4h14v1L8 9 1 5zM1 6.5l7 4 7-4V12H1z"/></svg>info@ridgelinehaulage.com.au</li>
      <li><svg viewBox="0 0 16 16"><circle cx="8" cy="8" r="7"/></svg>www.ridgelinehaulage.com.au</li>
    </ul>
    <div class="depot-band">DEPOT :RHS LOT 114, QUARRY FLAT ROAD, DUSTWATER, AUSTRALIA</div>
  </section>

  <section class="card card--back">
    <div class="photo" role="img" aria-label="Photo of a heavy haulage truck carrying earthmoving machinery"></div>
    <div class="services-banner"></div>
    <div class="services-title">OUR SER VICES</div>
    <ul class="services">
      <li>Over size load / Hot Shot Load</li>
      <li>Heavy Vehicle Recovery services</li>
      <li>potable water delivers</li>
      <li>Road Building / Maintenance</li>
      <li>Earthworks</li>
      <li>Send &amp; Metal Supply &amp; cartage</li>
      <li>Road train Trippers</li>
      <li>Road train Tankers</li>
      <li>Road train flat tops</li>
      <li>Drop Deck Trailers</li>
      <li>Mine site accredited equipment &amp; oparetors</li>
    </ul>
  </section>
</body>
</html>
```